Real Estate agent needs flyer/folder to contain bio and overview of services

I'm including files of the layout of the small folder. The folder is 6 1/2 across and 9 1/2 inches long. It will have a front & back cover and then writing on the 2 inside pages.

I am sending a few files to incorporate into the flyer, 1 new logo to use and 2 files which are coloring ideas.

Colors

Designer to choose colors to be used in the design.

```html
<!DOCTYPE html>
<html lang="en">
<head>
<meta charset="utf-8">
<title>Dana Moretti – Realtor Folder</title>
<link href="https://fonts.googleapis.com/css2?family=Libre+Baskerville:ital,wght@0,400;0,700;1,400&family=Open+Sans:ital,wght@0,400;0,600;1,400&display=swap" rel="stylesheet">
<style>
  :root{
    --navy:#1f3e85;
    --navy-deep:#162f6b;
    --mid-blue:#5b86c9;
    --light-blue:#9db8e6;
    --paper:#ffffff;
    --paper-grey:#f2f2f2;
    --ink:#2a2a2a;
    --stage:#e7e5e2;
  }
  *{box-sizing:border-box;margin:0;padding:0}
  html,body{width:826px;height:1200px;overflow:hidden;background:var(--stage)}
  .canvas{position:relative;width:826px;height:1200px;overflow:hidden;background:var(--stage);font-family:"Open Sans",Arial,sans-serif;color:var(--ink)}
  .spread{position:absolute;left:61px;width:701px;box-shadow:0 3px 10px rgba(0,0,0,.18)}
  .spread svg.art{position:absolute;inset:0;width:100%;height:100%}
  .cover{top:62px;height:509px}
  .inside{top:614px;height:512px}
  .abs{position:absolute}

  /* cover — back panel */
  .brand-mark{left:0;width:350px;top:248px;text-align:center;font-family:"Libre Baskerville",Georgia,serif;font-weight:700;font-size:15px;color:var(--navy)}
  .brand-mark .dot{display:inline-block;width:10px;height:10px;border-radius:50%;background:var(--navy);margin-right:7px;vertical-align:middle}
  .back-note{left:45px;width:260px;top:305px;text-align:center;font-family:"Libre Baskerville",Georgia,serif;font-style:italic;font-size:11.2px;line-height:1.3;color:var(--navy)}
  .agent-name{left:132px;top:452px;font-size:10.5px;font-weight:600;color:var(--light-blue);letter-spacing:.3px}
  .contact-row{left:16px;top:489px;display:flex;gap:28px;font-size:7.6px;color:#fff;align-items:center}
  .contact-row span{display:flex;align-items:center;gap:6px}
  .contact-row svg{width:10px;height:10px}

  /* cover — front panel */
  .front-name{left:350px;width:351px;top:50px;text-align:center;font-family:"Libre Baskerville",Georgia,serif;font-size:19px;color:var(--navy)}
  .headline{left:350px;width:351px;top:440px;text-align:center;font-family:"Libre Baskerville",Georgia,serif;font-weight:700;font-size:20px;line-height:1.32;color:#fff}

  /* inside */
  .bio{left:127px;top:45px;width:207px;color:#fff}
  .bio h3{font-family:"Libre Baskerville",Georgia,serif;font-weight:400;font-size:10.5px;margin-bottom:7px}
  .bio p{font-size:5.6px;line-height:1.22;margin-bottom:5px;text-align:justify}
  .column{width:320px}
  .column h2{font-family:"Libre Baskerville",Georgia,serif;font-weight:400;font-size:10.5px;color:var(--mid-blue);text-align:center;margin-bottom:4px}
  .column h4{font-size:10.5px;font-weight:400;color:var(--navy);text-align:center;margin-bottom:10px}
  .column p{font-size:6.1px;line-height:1.3;margin-bottom:9px;text-align:justify}
  .col-left{left:16px}
  .col-right{left:367px}
  .quote{width:320px;text-align:center;color:#fff;font-style:italic;font-size:5.8px;line-height:1.3}
  .quote .mark{display:block;font-family:"Libre Baskerville",Georgia,serif;font-style:normal;font-weight:700;font-size:16px;line-height:1;color:var(--light-blue);margin-bottom:2px}
  .quote .by{display:block}
</style>
</head>
<body>
<main class="canvas">

  <!-- Outer cover: back panel (left) and front panel (right) -->
  <section class="spread cover">
    <svg class="art" viewBox="0 0 701 509" preserveAspectRatio="none" aria-hidden="true">
      <defs>
        <linearGradient id="villaTones" x1="0" y1="0" x2="0" y2="1">
          <stop offset="0" stop-color="#23355f"/>
          <stop offset=".45" stop-color="#7a6142"/>
          <stop offset=".7" stop-color="#c9a36b"/>
          <stop offset="1" stop-color="#2f5f9e"/>
        </linearGradient>
      </defs>
      <rect x="0" y="0" width="350" height="509" fill="var(--paper-grey)"/>
      <rect x="350" y="0" width="351" height="509" fill="var(--paper)"/>
      <line x1="350" y1="0" x2="350" y2="430" stroke="#dcdcdc" stroke-width="1"/>
      <path d="M350 82 Q520 140 701 152 L701 160 Q520 150 350 96 Z" fill="var(--mid-blue)"/>
      <path d="M350 118 Q520 158 701 164 L701 420 L350 420 Z" fill="url(#villaTones)" role="img" aria-label="Photo of a luxury villa at dusk with a lit pool"/>
      <path d="M0 430 Q350 388 701 410" fill="none" stroke="var(--light-blue)" stroke-width="3"/>
      <path d="M0 440 Q350 398 701 418 L701 509 L0 509 Z" fill="var(--navy)"/>
    </svg>

    <div class="abs brand-mark"><span class="dot"></span>Brightwater Realty</div>
    <p class="abs back-note">Along with being your Realtor, I'm a lifelong resource for all things home-related &amp; beyond…if you need a great referral for anything at all, call me! I can't wait to work with you!</p>

    <div class="abs front-name">Dana Moretti</div>

    <div class="abs agent-name">DANA MORETTI</div>
    <div class="abs contact-row">
      <span><svg viewBox="0 0 10 10"><circle cx="5" cy="5" r="4.3" fill="none" stroke="#fff" stroke-width=".8"/><path d="M1 5h8M5 .7c-2 2.6-2 6 0 8.6M5 .7c2 2.6 2 6 0 8.6" fill="none" stroke="#fff" stroke-width=".6"/></svg>www.danamhomes.com</span>
      <span><svg viewBox="0 0 10 10"><circle cx="5" cy="5" r="4.3" fill="none" stroke="#fff" stroke-width=".8"/><path d="M3.4 2.8l1 1-.6.7c.4.8 1 1.4 1.8 1.8l.7-.6 1 1-.8.8C4.9 7.3 2.7 5.1 2.6 3.6z" fill="#fff"/></svg>555 010 2748</span>
      <span><svg viewBox="0 0 10 10"><circle cx="5" cy="5" r="4.3" fill="none" stroke="#fff" stroke-width=".8"/><rect x="2.6" y="3.4" width="4.8" height="3.4" fill="none" stroke="#fff" stroke-width=".6"/><path d="M2.6 3.4L5 5.3l2.4-1.9" fill="none" stroke="#fff" stroke-width=".6"/></svg>dana@danamhomes.com</span>
    </div>
    <h1 class="abs headline">Helping You<br>Make Better Decisions…</h1>
  </section>

  <!-- Inside spread -->
  <section class="spread inside">
    <svg class="art" viewBox="0 0 701 512" preserveAspectRatio="none" aria-hidden="true">
      <defs>
        <linearGradient id="nightTones" x1="0" y1="0" x2="1" y2="1">
          <stop offset="0" stop-color="#1a2b55"/>
          <stop offset="1" stop-color="#0d1a38"/>
        </linearGradient>
        <linearGradient id="loungeTones" x1="0" y1="0" x2="1" y2="1">
          <stop offset="0" stop-color="#6a4a3a"/>
          <stop offset=".5" stop-color="#8a7fb0"/>
          <stop offset="1" stop-color="#3a3f6e"/>
        </linearGradient>
        <linearGradient id="portraitTones" x1="0" y1="0" x2="0" y2="1">
          <stop offset="0" stop-color="#d8b879"/>
          <stop offset=".6" stop-color="#c9a08a"/>
          <stop offset="1" stop-color="#2b2b2f"/>
        </linearGradient>
      </defs>
      <rect x="0" y="0" width="701" height="512" fill="var(--paper)"/>
      <rect x="0" y="0" width="350" height="512" fill="#f6f6f6"/>
      <path d="M0 0 H350 V160 Q180 182 0 190 Z" fill="url(#nightTones)" role="img" aria-label="Evening pool terrace backdrop"/>
      <path d="M0 36 Q60 30 116 40 L116 185 Q60 189 0 190 Z" fill="url(#portraitTones)" opacity=".9" role="img" aria-label="Portrait of the agent"/>
      <path d="M0 190 Q180 182 350 160" fill="none" stroke="var(--mid-blue)" stroke-width="3"/>
      <path d="M350 0 H701 V118 Q520 140 350 152 Z" fill="url(#loungeTones)" role="img" aria-label="Photo of lounge chairs beside an indoor pool"/>
      <path d="M350 152 Q520 140 701 118 L701 126 Q520 150 350 160 Z" fill="var(--navy)"/>
      <line x1="350" y1="160" x2="350" y2="445" stroke="#dedede" stroke-width="1"/>
      <path d="M0 448 Q350 430 701 448 L701 512 L0 512 Z" fill="var(--navy)"/>
      <line x1="350" y1="439" x2="350" y2="512" stroke="var(--navy-deep)" stroke-width="1.5"/>
    </svg>

    <div class="abs bio">
      <h3>Let me introduce myself</h3>
      <p>I'm originally from Milwaukee, but I'm a full-fledged coastal girl now. I've lived and worked in Bayshore County since 2001. I always say where we live is the next best thing to living on a tropical island. I've traveled to many and I'm always happy to come back to my Harbor Crest home.</p>
      <p>My passion for this area is why I'm in Real Estate. I consider myself incredibly fortunate to sell homes and help people purchase homes in an area that I love with all my heart.</p>
      <p>This passion also carries over in representing my clients with the highest degree of professionalism, enthusiasm and care. My business is built on exceptional customer service and I'm grateful my clients are mostly repeat and referrals.</p>
    </div>

    <div class="abs column col-left" style="top:215px">
      <h2>My Core Tenet</h2>
      <h4>It's All About YOU!</h4>
      <p>My #1 priority is understanding YOUR needs and YOUR objectives. This understanding, along with working diligently on your behalf, means we accomplish your goal whether you're purchasing your 1st home or selling a home you've loved so you can move on to the next chapter of your life.</p>
    </div>

    <div class="abs column col-left" style="top:306px">
      <h2 style="margin-bottom:12px">Real Estate Services &amp; Beyond…</h2>
      <p>Simply put, I help people who are local, relocating and investing, sell and purchase homes in the Bayshore region. For purchases outside of the state, I can refer to a network of agents across the country.</p>
      <p>I also provide a team who is dedicated to providing outstanding customer service throughout the transaction. My team includes a network of lenders, title, and escrow officers, in house CPA, stagers, photographers, contractors and more.</p>
    </div>

    <div class="abs column col-right" style="top:157px">
      <h2 style="margin-bottom:7px">Selling Your Home</h2>
      <p>Selling your home is not like any other business transaction. It's also personal. My priority as your Listing Agent is to guide you through what can be a complicated and sometimes emotional process.</p>
      <p>I place great emphasis on marketing your property with professional photographs, along with harnessing the power of the Internet and the virtual world to reach as many buyers as possible. Your property will be marketed to the public as well as to other agents, thus creating maximum exposure of your home.</p>
      <p>When we first meet to discuss selling your home, it's essential for me to gain an understanding of your unique needs such as timelines, expectations and financial considerations, just to name a few. From there, I begin the process of listing and marketing your home. I lead you through negotiations and more paperwork than you ever care to do, guiding you to the successful closing of your home.</p>
    </div>

    <div class="abs column col-right" style="top:297px">
      <h2 style="margin-bottom:12px">Buying a Home</h2>
      <p>If you're thinking about buying a home, it's imperative you have an accomplished, real estate professional by your side to walk you through what is likely the largest purchase of your life.</p>
      <p>To get started, I like to meet with you so we have an opportunity to get to know each other as purchasing a home is a uniquely, personal endeavor. At that time, we can discuss your goals and if it's a good time for you to purchase a home.</p>
      <p>From there, the first step is to obtain a pre-approval from a lender. I'm able to recommend various lenders who can introduce and explain the various loan products available. After you've been pre-approved, that's when the fun starts! I guide you through the home buying adventure every step of the way and look forward to handing you the keys to your new home.</p>
    </div>

    <blockquote class="abs quote" style="left:15px;top:452px">
      <span class="mark">“</span>
      Dana is the kind of Real Estate professional everyone wants to represent them. She is knowledgeable, ethical, energetic, and follows up on every detail. Her honesty, integrity and expertise combined make her a very special and remarkable professional. We were lucky to find her!
      <span class="by">Greg &amp; Alana Whitcombe</span>
    </blockquote>
    <blockquote class="abs quote" style="left:366px;top:452px">
      <span class="mark">“</span>
      During the home buying process, Dana becomes your trusted advisor, mentor and friend. Her knowledge of the industry, community and market are best in class. A true professional! Dana aligned her goals with my own and understood the motivation behind my purchase. Dana is unequivocally the reason why I was able to purchase my home in Harbor Crest and provide my family with a world-class community.
      <span class="by">Reuben Castellano</span>
    </blockquote>
  </section>

</main>
</body>
</html>
```